BuildLinkHub.com Full Stationery Design

Business Card will have all info on it. Letterhead will not have name, title or mobile number. Keep general feeling very clean, using colors from the logo as accents.
Name:Dale Marchetti
Title:President
Phone: 1-800-555-0142
Cell: 306-555-0187
email: dale@buildlinkhub.example
website: www.buildlinkhub.example
Address:
PO Box 947
Kestrel Bay, SK
S0J2T0

Target Market(s)

Construction Business owners

Industry/Entity Type

Business

Contact Information for Business Card

Name:Dale Marchetti
Title:President
Phone: 1-800-555-0142
Cell: 306-555-0187
Address:
PO Box 947
Kestrel Bay, SK
S0J2T0

Font styles to use
Sans Serif

Requirements
Must have
• Clean look
Should not have
• Images or cartoon type characters or tools

```html
<!DOCTYPE html>
<html lang="en">
<head>
<meta charset="utf-8">
<title>BuildLinkHub.com Business Card</title>
<link rel="stylesheet" href="https://fonts.googleapis.com/css2?family=Open+Sans:wght@400;600;700&display=swap">
<style>
  :root {
    --slate: #4a5769;
    --slate-dark: #485868;
    --orange: #e8502a;
    --text: #4d4f53;
    --paper: #ffffff;
    --stage: #e9e7e3;
  }
  * { margin: 0; padding: 0; box-sizing: border-box; }
  html, body {
    width: 1200px; height: 987px; overflow: hidden;
    background: var(--stage);
    font-family: "Open Sans", sans-serif;
  }
  .card {
    position: absolute; left: 293px;
    width: 615px; height: 351px;
    box-shadow: 0 2px 6px rgba(0,0,0,.25);
  }
  .card-front { top: 130px; background: var(--paper); }
  .card-back { top: 506px; background: var(--slate-dark); }

  .brand {
    position: absolute; display: flex; align-items: center; gap: 12px;
    font-weight: 700; font-size: 30px; letter-spacing: -0.2px;
    white-space: nowrap;
  }
  .brand-square { width: 34px; height: 34px; background: var(--orange); flex: none; }
  .card-front .brand { left: 45px; top: 52px; color: var(--slate); }
  .card-back .brand {
    left: 0; right: 0; top: 150px; justify-content: center; color: #fff;
  }

  .contact {
    position: absolute; left: 46px; top: 175px;
    font-size: 15px; line-height: 23px; color: var(--text);
    white-space: nowrap;
  }
  .contact .address { margin-bottom: 3px; }
  .contact .row { display: flex; align-items: center; gap: 8px; height: 24px; }
  .contact svg { width: 14px; height: 14px; fill: var(--slate); flex: none; }

  .person {
    position: absolute; right: 37px; top: 205px; text-align: right;
    white-space: nowrap;
  }
  .person-name { font-size: 21px; font-weight: 700; color: var(--slate); }
  .person-title { font-size: 15px; color: var(--orange); margin-top: 1px; }

  .footer-band { position: absolute; left: 0; bottom: 0; width: 615px; height: 41px; }
  .footer-url {
    position: absolute; right: 31px; bottom: 10px;
    color: #fff; font-size: 16px; white-space: nowrap;
  }
  .back-url {
    position: absolute; left: 0; right: 0; top: 288px; text-align: center;
    color: #fff; font-size: 16px;
  }
</style>
</head>
<body>
  <section class="card card-front">
    <div class="brand"><span class="brand-square"></span><span>BuildLinkHub.com</span></div>

    <div class="contact">
      <p class="address">PO Box 947<br>Kestrel Bay, SK, S0J2T0</p>
      <p class="row">
        <svg viewBox="0 0 16 16" aria-hidden="true"><path d="M3.6 1.2l2.3 2.6-1.3 1.8c.9 2 2.5 3.7 4.6 4.7l1.8-1.3 2.6 2.3-1.2 2.4C6.8 13.4 2.6 9.2 1.2 3.6z"/></svg>
        1-800-555-0142
      </p>
      <p class="row">
        <svg viewBox="0 0 16 16" aria-hidden="true"><path d="M4 0h8a1 1 0 0 1 1 1v14a1 1 0 0 1-1 1H4a1 1 0 0 1-1-1V1a1 1 0 0 1 1-1zm.8 2v10h6.4V2zM8 13a.9.9 0 1 0 0 1.8A.9.9 0 0 0 8 13z"/></svg>
        306-555-0187
      </p>
      <p class="row">
        <svg viewBox="0 0 16 16" aria-hidden="true"><path d="M1 3h14v10H1zm1.5 1.3v.4L8 8.6l5.5-3.9v-.4zm0 2v5.4h11V6.3L8 10.2z"/></svg>
        dale@buildlinkhub.example
      </p>
    </div>

    <div class="person">
      <p class="person-name">Dale Marchetti</p>
      <p class="person-title">President</p>
    </div>

    <svg class="footer-band" viewBox="0 0 615 41" aria-hidden="true">
      <path d="M0 27H318C348 27 340 0 372 0H601V41H0Z" fill="var(--slate)"/>
      <rect x="601" y="0" width="14" height="41" fill="var(--orange)"/>
    </svg>
    <p class="footer-url">buildlinkhub.example</p>
  </section>

  <section class="card card-back">
    <div class="brand"><span class="brand-square"></span><span>BuildLinkHub.com</span></div>
    <p class="back-url">www.buildlinkhub.example</p>
  </section>
</body>
</html>
```